Growing the Ironclad Young Contender:
A Family Playbook for Nurturing Bold, Grounded, and Resilient Daughters at Games and Beyond.
📘 Book Cover Design Brief – “Growing the Ironclad Young Contender”

Project Title:
Design a bold, inspiring book cover for a best-selling book titled:
Growing the Ironclad Young Contender
Subtitle: A Family Playbook for Nurturing Bold, Grounded, and Resilient Daughters at Games and Beyond

🎯 Audience:

Parents of female athletes ages 14–20 who want their daughters to build confidence, strength, resilience, and long-term success both in sports and in life.

This book should feel encouraging, empowering, and credible — NOT cheesy, childish, or overly academic.

📕 Design Tone & Style:

Powerful and professional — should feel like a best-selling book from a leading performance or parenting expert

Emotionally compelling — conveys hope, resilience, strength, and possibility

Visually modern and clean — avoid anything overly busy, cliché, or childish

Heroic/aspirational tone — think transformation, leadership, strong positioning

💡 Visual Direction / Ideas (Use as Inspiration, Not Limitation):

Strong, confident teenage female athlete imagery — adaptable beyond one specific sport

Symbolic visuals — e.g. athlete standing strong, on a starting line, looking bold into the future, silhouette, or power stance

Bold typography that feels clean and modern (e.g., Proxima Nova, Montserrat, Gotham, Bebas Neue, etc.)

A title that stands out clearly when viewed as a thumbnail on Brindlemart

Color tones: Empowering, modern, and strong: think deep blues, greens, purples, or golds — avoid playful pastels or overly girly themes

Potential imagery: textured backgrounds, motion, bravery, development, strength, growth, sport/action overlays

🔥 What the Cover MUST Communicate:

✅ This is for parents who want strong, confident female athletes
✅ It’s a guidebook for personal development AND sports performance
✅ It’s about creating “IRONCLAD” confidence — physically, mentally and emotionally
✅ The message is: You can help your daughter become her strongest, most confident self

📚 Back-of-Book Summary (for context):

"Growing the Ironclad Young Contender" is a parent's blueprint to building girls who are strong in body, confident in mind, and ready to lead on and off the field. Through simple strategies around strength training, mindset, nutrition, and character development, this book gives parents the tools to help their daughters stay injury-resistant, break through mental barriers, and unlock their full potential — in sports and in life.

✅ Deliverables:

Full cover design (front, back, spine) for paperback
High-resolution files (print-ready)
Source files (PSD, AI, etc.)
3D mockup versions of the book (standing, flat, stack)

Target Market(s)

Industry/Entity Type

Fitness

Font styles to use
Sans Serif

Colors
FFF300
FFF600
FEFA6F
FFFEC7
FFFEE8

Requirements
Must have
• Bold Font
Should not have
• I don't want an image of a female athlete. I want this to be font based.

```html
<!DOCTYPE html>
<html lang="en">
<head>
<meta charset="utf-8">
<title>Growing the Ironclad Young Contender – Paperback Cover</title>
<link rel="stylesheet" href="https://fonts.googleapis.com/css2?family=Anton&family=Montserrat:wght@600&family=Open+Sans:wght@400;700&display=swap">
<style>
  :root {
    --page-bg: #c9d0cf;
    --cover-dark: #1c2824;
    --cover-mid: #2b3a35;
    --cover-light: #3f4c48;
    --accent-yellow: #fef79a;
    --label-yellow: #fff6a8;
    --dot-teal: #3d5f55;
    --text-light: #e6ece9;
    --ink-dark: #23302b;
  }
  * { margin: 0; padding: 0; box-sizing: border-box; }
  html, body { width: 1200px; height: 800px; overflow: hidden; }
  body {
    background: var(--page-bg);
    display: flex; align-items: center; justify-content: center;
  }
  .cover-spread { display: flex; height: 720px; box-shadow: 0 10px 30px rgba(0,0,0,.25); }

  .panel {
    position: relative; height: 100%;
    background: linear-gradient(160deg, var(--cover-light) 0%, var(--cover-mid) 30%, var(--cover-dark) 70%);
  }

  /* back cover */
  .back-cover { width: 410px; }
  .publisher-label {
    position: absolute; left: 150px; top: 0; width: 112px; height: 140px;
    background: var(--label-yellow);
    display: flex; flex-direction: column; align-items: center; justify-content: center; gap: 10px;
  }
  .publisher-label .label-mark {
    width: 30px; height: 30px; border-radius: 50%; border: 2px solid var(--ink-dark);
  }
  .publisher-label .label-name {
    font-family: 'Open Sans', sans-serif; font-weight: 700; font-size: 11px;
    letter-spacing: 1px; color: var(--ink-dark);
  }
  .back-copy {
    position: absolute; left: 22px; right: 22px; top: 182px;
    font-family: 'Open Sans', sans-serif; color: var(--text-light);
    font-size: 11.5px; line-height: 1.35; letter-spacing: .4px;
  }
  .back-copy .copy-heading { font-weight: 700; font-size: 12px; letter-spacing: .8px; margin-bottom: 14px; }
  .back-copy .copy-point { margin-bottom: 13px; text-align: justify; }
  .back-copy .summary { margin-top: 48px; text-align: justify; }

  /* spine */
  .spine { width: 36px; background: linear-gradient(90deg, var(--cover-dark), #121b18); }
  .spine-text {
    position: absolute; left: 50%; top: 26px;
    writing-mode: vertical-rl;
    transform: translateX(-50%);
    display: flex; gap: 40px; align-items: center;
  }
  .spine-title {
    font-family: 'Open Sans', sans-serif; font-weight: 700; font-size: 10px;
    letter-spacing: 2px; color: var(--accent-yellow);
  }
  .spine-author {
    font-family: 'Montserrat', sans-serif; font-weight: 600; font-size: 11px;
    letter-spacing: 6px; color: var(--accent-yellow);
  }
  .spine-badge {
    position: absolute; left: 8px; bottom: 10px; width: 20px; height: 76px;
    background: var(--label-yellow);
  }

  /* front cover */
  .front-cover { width: 410px; }
  .corner-bracket { position: absolute; border-color: var(--accent-yellow); border-style: solid; border-width: 0; }
  .corner-bracket.top-left { left: 24px; top: 30px; width: 58px; height: 124px; border-top-width: 3px; border-left-width: 3px; }
  .corner-bracket.bottom-right { right: 24px; bottom: 20px; width: 62px; height: 126px; border-bottom-width: 3px; border-right-width: 3px; }
  .dot-field { position: absolute; }
  .dot-field.top { right: 10px; top: 22px; }
  .dot-field.bottom { right: 10px; bottom: 32px; }
  .cover-title { position: absolute; left: 52px; top: 178px; width: 306px; }
  .cover-title text { font-family: 'Anton', sans-serif; }
  .cover-title .title-accent { fill: var(--accent-yellow); }
  .cover-title .title-key { fill: #ffffff; }
  .cover-subtitle {
    position: absolute; left: 40px; right: 40px; top: 536px; text-align: center;
    font-family: 'Open Sans', sans-serif; font-weight: 700; font-size: 10.5px;
    line-height: 1.45; letter-spacing: 1.2px; text-transform: uppercase; color: var(--accent-yellow);
  }
  .cover-author {
    position: absolute; left: 0; right: 0; top: 612px; text-align: center;
    font-family: 'Montserrat', sans-serif; font-weight: 600; font-size: 17px;
    letter-spacing: 5px; color: var(--accent-yellow);
  }
</style>
</head>
<body>
<main class="cover-spread">

  <section class="panel back-cover" aria-label="Back cover">
    <div class="publisher-label">
      <span class="label-mark"></span>
      <span class="label-name">IRONCLAD</span>
    </div>
    <div class="back-copy">
      <p class="copy-heading">What the Cover MUST Communicate:</p>
      <p class="copy-point">This is for parents who want strong, confident female athletes</p>
      <p class="copy-point">It’s a guidebook for personal development AND sports performance</p>
      <p class="copy-point">It’s about creating “IRONCLAD” confidence—physically, mentally and emotionally</p>
      <p class="copy-point">The message is: You can help your daughter become her strongest, most confident self</p>
      <p class="summary">"Growing the Ironclad Young Contender" is a parent's blueprint to building girls who are strong in body, confident in mind, and ready to lead on and off the field. Through simple strategies around strength training, mindset, nutrition, and character development, this book gives parents the tools to help their daughters stay injury-resistant, break through mental barriers, and unlock their full potential — in sports and in life.</p>
    </div>
  </section>

  <section class="panel spine" aria-label="Spine">
    <div class="spine-text">
      <span class="spine-title">GROWING THE IRONCLAD YOUNG CONTENDER</span>
      <span class="spine-author">author name</span>
    </div>
    <div class="spine-badge"></div>
  </section>

  <section class="panel front-cover" aria-label="Front cover">
    <div class="corner-bracket top-left"></div>
    <div class="corner-bracket bottom-right"></div>

    <svg class="dot-field top" width="290" height="78" viewBox="0 0 290 78" aria-hidden="true">
      <g fill="var(--dot-teal)">
        <circle cx="10" cy="10" r="6"/><circle cx="36" cy="10" r="6"/><circle cx="62" cy="10" r="6"/><circle cx="88" cy="10" r="6"/><circle cx="114" cy="10" r="6"/><circle cx="140" cy="10" r="6"/><circle cx="166" cy="10" r="6"/><circle cx="192" cy="10" r="6"/><circle cx="218" cy="10" r="6"/><circle cx="244" cy="10" r="6"/>
        <circle cx="88" cy="36" r="6"/><circle cx="114" cy="36" r="6"/><circle cx="140" cy="36" r="6"/><circle cx="166" cy="36" r="6"/><circle cx="192" cy="36" r="6"/><circle cx="218" cy="36" r="6"/><circle cx="244" cy="36" r="6"/><circle cx="270" cy="36" r="6"/>
        <circle cx="166" cy="62" r="6"/><circle cx="192" cy="62" r="6"/><circle cx="218" cy="62" r="6"/><circle cx="244" cy="62" r="6"/><circle cx="270" cy="62" r="6"/>
      </g>
    </svg>

    <svg class="cover-title" viewBox="0 0 306 340" role="heading" aria-level="1" aria-label="Growing the Ironclad Young Contender">
      <text class="title-accent" x="0" y="66" font-size="74" textLength="306" lengthAdjust="spacingAndGlyphs">GROWING THE</text>
      <text class="title-key" x="14" y="134" font-size="62" textLength="278" lengthAdjust="spacingAndGlyphs">IRONCLAD</text>
      <text class="title-accent" x="10" y="236" font-size="104" textLength="286" lengthAdjust="spacingAndGlyphs">YOUNG</text>
      <text class="title-accent" x="0" y="330" font-size="92" textLength="306" lengthAdjust="spacingAndGlyphs">CONTENDER</text>
    </svg>

    <p class="cover-subtitle">A Family Playbook for Nurturing Bold, Grounded, and Resilient Daughters at Games and Beyond</p>
    <p class="cover-author">author name</p>

    <svg class="dot-field bottom" width="300" height="56" viewBox="0 0 300 56" aria-hidden="true">
      <g fill="var(--dot-teal)">
        <circle cx="110" cy="10" r="6"/><circle cx="136" cy="10" r="6"/><circle cx="162" cy="10" r="6"/><circle cx="188" cy="10" r="6"/><circle cx="214" cy="10" r="6"/><circle cx="240" cy="10" r="6"/><circle cx="266" cy="10" r="6"/><circle cx="290" cy="10" r="6"/>
        <circle cx="10" cy="38" r="6"/><circle cx="36" cy="38" r="6"/><circle cx="62" cy="38" r="6"/><circle cx="88" cy="38" r="6"/><circle cx="114" cy="38" r="6"/><circle cx="140" cy="38" r="6"/><circle cx="166" cy="38" r="6"/><circle cx="192" cy="38" r="6"/><circle cx="218" cy="38" r="6"/><circle cx="244" cy="38" r="6"/>
      </g>
    </svg>
  </section>

</main>
</body>
</html>
```